US company marketing to law enforcement needs brochure design

We have created a new logo and now need to update our printed material. What we really need is a "style" or "template" for how our brochures will look in the future. Enclosed is the brochure draft with the old style and logo. Also enclosed is the new logo. As we are marketing to US law enforcement it is important the the brochure design is strong, powerful and that we are looking experienced and trustworthy. However, we also want to look modern in line with the logo update.

Target Market(s)

Law enforcement

Industry/Entity Type

Marketing

```html
<!DOCTYPE html>
<html lang="en">
<head>
<meta charset="utf-8">
<title>Meridian Justice – Brochure Cover</title>
<link rel="stylesheet" href="https://fonts.googleapis.com/css2?family=Ubuntu:wght@400;500&display=swap">
<style>
  :root {
    --navy: #1f3a6e;
    --orange: #d9531e;
    --grey-text: #6d6f72;
    --brand-grey: #8d8f92;
    --faint: #eef0f5;
    --faint-text: #ffffff;
    --paper: #ffffff;
    --backdrop: #e8e5e0;
    --fold: #d3d3d6;
    --photo-deep: #3e0f04;
    --photo-dark: #7a2208;
    --photo-mid: #c24512;
    --photo-light: #ee8a35;
    --photo-gold: #f3c173;
  }
  * { margin: 0; padding: 0; box-sizing: border-box; }
  html, body { width: 1200px; height: 868px; overflow: hidden; background: var(--backdrop); }
  body { font-family: "Ubuntu", sans-serif; position: relative; }

  .brochure {
    position: absolute; left: 20px; top: 24px;
    width: 1160px; height: 820px;
    background: var(--paper);
    overflow: hidden;
  }
  .panel { position: absolute; top: 0; height: 804px; }
  .panel--back { left: 0; width: 579px; }
  .panel--front { left: 579px; width: 581px; border-left: 1px solid var(--fold); }

  .back-disc {
    position: absolute; left: 33px; top: 88px;
    width: 494px; height: 494px; border-radius: 50%;
    background: var(--faint);
    display: flex; align-items: center; justify-content: center;
  }
  .back-disc__name {
    font-size: 62px; font-weight: 500; line-height: 1.05;
    color: var(--faint-text); text-align: center; letter-spacing: -0.5px;
  }

  .brand {
    position: absolute; top: 690px;
    display: flex; align-items: center; gap: 20px;
  }
  .panel--back .brand { left: 124px; }
  .panel--front .brand { left: 83px; }
  .brand__dot { width: 67px; height: 67px; border-radius: 50%; background: var(--navy); flex: none; }
  .brand__name { font-size: 37px; font-weight: 500; color: var(--brand-grey); letter-spacing: -0.5px; white-space: nowrap; }

  .cover-art { position: absolute; left: 0; top: 0; width: 581px; height: 424px; display: block; }

  .tagline {
    position: absolute; left: 67px; top: 459px; width: 431px; height: 56px;
    border-top: 1px solid var(--navy); border-bottom: 1px solid var(--navy);
    display: flex; align-items: center; justify-content: center;
    font-size: 24px; font-weight: 400; color: var(--grey-text); white-space: nowrap;
  }

  .programs { position: absolute; left: 0; top: 574px; width: 581px; }
  .programs__row {
    list-style: none; text-align: center;
    font-size: 20px; color: var(--navy); line-height: 42px; white-space: nowrap;
  }
  .programs__row li { display: inline; }
  .programs__row li + li::before { content: "•"; color: #9a9ca0; margin: 0 15px; }

  .base-band { position: absolute; left: 0; bottom: 0; width: 1160px; height: 16px; background: var(--navy); }
  .corner-peak { position: absolute; left: 49px; bottom: 16px; width: 82px; height: 41px; display: block; }
</style>
</head>
<body>
  <div class="brochure">
    <section class="panel panel--back">
      <div class="back-disc">
        <span class="back-disc__name">Meridian<br>Justice</span>
      </div>
      <div class="brand">
        <span class="brand__dot"></span>
        <span class="brand__name">Meridian Justice</span>
      </div>
    </section>

    <section class="panel panel--front">
      <svg class="cover-art" viewBox="0 0 581 424">
        <defs>
          <linearGradient id="desk-base" x1="0" y1="0" x2="0" y2="1">
            <stop offset="0" stop-color="var(--photo-dark)"/>
            <stop offset="0.45" stop-color="var(--photo-mid)"/>
            <stop offset="1" stop-color="var(--photo-deep)"/>
          </linearGradient>
          <radialGradient id="lamp-glow" cx="0.42" cy="0.42" r="0.55">
            <stop offset="0" stop-color="var(--photo-light)" stop-opacity="0.95"/>
            <stop offset="1" stop-color="var(--photo-light)" stop-opacity="0"/>
          </radialGradient>
          <radialGradient id="brass-glow" cx="0.88" cy="0.35" r="0.4">
            <stop offset="0" stop-color="var(--photo-gold)" stop-opacity="0.85"/>
            <stop offset="1" stop-color="var(--photo-gold)" stop-opacity="0"/>
          </radialGradient>
        </defs>
        <g role="img" aria-label="Photograph of a wooden judge's gavel beside brass scales of justice on a warm lit desk">
          <rect x="0" y="0" width="581" height="424" fill="url(#desk-base)"/>
          <rect x="0" y="0" width="581" height="424" fill="url(#lamp-glow)"/>
          <rect x="0" y="0" width="581" height="424" fill="url(#brass-glow)"/>
        </g>
        <polygon points="0,416 241,416 280,376 322,416 581,416 581,424 0,424" fill="var(--paper)"/>
        <polyline points="0,400 241,400 280,360 322,400 581,400" fill="none" stroke="var(--navy)" stroke-width="3"/>
        <polyline points="0,406 241,406 280,366 322,406 581,406" fill="none" stroke="var(--orange)" stroke-width="3"/>
        <polyline points="0,413 241,413 280,373 322,413 581,413" fill="none" stroke="var(--navy)" stroke-width="5"/>
      </svg>

      <h1 class="tagline">Comprehensive Offender Programs</h1>

      <div class="programs">
        <ul class="programs__row">
          <li>Pre Trial</li><li>Diversion</li><li>Deferred Prosecution</li>
        </ul>
        <ul class="programs__row">
          <li>Jail Alternative</li><li>Probation</li>
        </ul>
      </div>

      <div class="brand">
        <span class="brand__dot"></span>
        <span class="brand__name">Meridian Justice</span>
      </div>
    </section>

    <svg class="corner-peak" viewBox="0 0 82 41"><polygon points="0,41 41,0 82,41" fill="var(--navy)"/></svg>
    <div class="base-band"></div>
  </div>
</body>
</html>
```